A Vegan Nutritional Supplement (one Product) website

I am looking for an experienced Web designer to build a One Product website for a Nutritional Supplement that is 100% vegan. The emphasis would be on both the Quality and Quantity of the ingredients and their benefits. It contains Essential Vitamins, Minerals, and a proprietary blend of 42 Fruits and Vegetables. I welcome color suggestions as long as it includes Green (vegan) and White.. The final design should communicate to the buyer: Quality, Healthy, Safety (Natural vegan ingredients), Natural energy, well being. The product includes benefits for 3 vital elements of optimal health: Immune Health, Heart Health, and Brain Health

Industry/Entity Type

Health and Wellness - Nutritional Supplements

Number of Pages Required

4 page

Other font styles liked:
• I Welcome your creativity

Colors
59FF00
82FF00
B8FF75
E3FFCB
F4FFEA

Requirements
Must have
• Options to purchase : One product ($34.95); 2 products ($31.45 each - 10% discount), or 3 Products ($27.95 each - 20% discount)
Nice to have
• Focus on the Benefits of having all these Ingredients - Nutrients in one bottle - Essential Vitamins, Minerals, and proprietary blend of 42 Fruits and Vegetables.

```html
<!DOCTYPE html>
<html lang="en">
<head>
<meta charset="utf-8">
<title>Green Vigor — 100% Vegan Supplement</title>
<link rel="stylesheet" href="https://fonts.googleapis.com/css2?family=Josefin+Sans:wght@600;700&family=Lato:wght@400;700&display=swap">
<style>
:root{
  --green:#3c9634;
  --green-deep:#2a7226;
  --forest:#285a25;
  --lime:#c9dc14;
  --lime-soft:#f4f7c8;
  --star:#f2a21b;
  --ink:#1d1d1d;
  --soft-grey:#f2f2f2;
  --panel-grey:#e6e6e6;
  --white:#fff;
  --black:#000;
}
*{margin:0;padding:0;box-sizing:border-box}
html,body{width:1200px;height:4216px;overflow:hidden}
body{position:relative;font-family:"Lato",sans-serif;color:var(--ink);background:var(--white)}
h1,h2,h3{font-family:"Josefin Sans",sans-serif;font-weight:700}
.placeholder{position:absolute}

/* brand */
.brand{position:absolute;display:flex;align-items:center;gap:10px;color:var(--white);font-family:"Josefin Sans",sans-serif;font-weight:700;line-height:1;white-space:nowrap}
.brand i{display:block;background:var(--lime)}
.hero .brand{left:111px;top:34px;font-size:24px}
.hero .brand i{width:16px;height:16px}

/* hero */
.hero{position:absolute;left:0;top:0;width:1200px;height:727px;background:linear-gradient(180deg,#46a23a 0%,#3a8f31 55%,#2f7f2a 100%)}
.nav{position:absolute;top:37px;left:370px;display:flex;gap:40px;color:var(--white);font-size:15px}
.account{position:absolute;top:37px;left:934px;color:var(--white);font-size:15px;display:flex;gap:14px}
.cart-dot{position:absolute;left:1053px;top:28px;width:36px;height:36px;border-radius:50%;background:var(--lime)}
.hero h1{position:absolute;left:111px;top:258px;color:var(--white);font-size:54px;line-height:66px}
.hero p{position:absolute;left:111px;top:392px;width:470px;color:var(--white);font-size:15px;line-height:26px}
.btn-lime{position:absolute;background:var(--lime);color:var(--white);font-weight:700;border-radius:26px;display:flex;align-items:center;justify-content:center}
.hero .btn-lime{left:111px;top:455px;width:146px;height:48px;font-size:15px}
.hero-circle{position:absolute;left:598px;top:120px;width:562px;height:562px;border-radius:50%;background:#8fc21f}
.hero-product{left:635px;top:183px;width:449px;height:447px;border-radius:30px;background:linear-gradient(180deg,#f2f2f2 0%,#6aa64a 40%,#2f7a2b 100%)}

/* product */
.thumb{position:absolute;left:95px;width:108px;height:95px;background:var(--panel-grey)}
.thumb.active{border:3px solid var(--lime);background:var(--white)}
.thumb i{position:absolute;left:38px;top:14px;width:32px;height:66px;border-radius:6px;background:linear-gradient(180deg,#eee 0 25%,#3d8a33 25%)}
.main-shot{position:absolute;left:213px;top:797px;width:378px;height:549px;background:var(--panel-grey)}
.main-shot .placeholder{left:55px;top:30px;width:268px;height:480px;border-radius:30px;background:linear-gradient(180deg,#f4f4f4 0 18%,#3f8b35 18%,#2c6b28 100%)}
.product-title{position:absolute;left:614px;top:802px;font-size:33px}
.product-sub{position:absolute;left:615px;top:845px;font-size:16px;color:#aaa}
.stars{position:absolute;display:flex;gap:5px}
.stars svg{width:15px;height:15px;fill:var(--star)}
.size-label{position:absolute;left:617px;top:919px;font-size:17px}
.pack{position:absolute;top:966px;height:41px;border:1.5px solid #999;font-size:15px;display:flex;align-items:center;justify-content:center;background:var(--white)}
.pack.active{background:var(--forest);color:var(--white);border-color:var(--forest)}
.qty{position:absolute;left:625px;top:1063px;font-size:16px;font-weight:700}
.qty-box{position:absolute;left:722px;top:1056px;width:90px;height:32px;border-radius:16px;background:var(--soft-grey);display:flex;justify-content:space-around;align-items:center;font-size:16px;font-weight:700}
.cart-btn{left:625px;top:1126px;width:145px;height:46px;font-size:16px}
.price{position:absolute;left:791px;top:1137px;font-size:18px;font-weight:700}
.rule{position:absolute;left:614px;top:1205px;width:493px;height:1px;background:#ddd}
.details-title{position:absolute;left:623px;top:1228px;font-size:21px}
.details-text{position:absolute;left:623px;top:1260px;width:380px;font-size:13px;line-height:23px}

/* features */
.features{position:absolute;left:0;top:1421px;width:1200px;height:614px;background:var(--soft-grey)}
.section-title{position:absolute;left:0;width:1200px;text-align:center;color:var(--ink)}
.features .section-title{top:60px;font-size:36px;line-height:45px}
.feature{position:absolute;top:215px;width:210px;text-align:center}
.feature .icon{width:68px;height:68px;border-radius:50%;border:4px solid var(--forest);margin:0 auto 18px;display:flex;align-items:center;justify-content:center;background:var(--white)}
.feature h3{font-family:"Lato",sans-serif;font-weight:700;font-size:17px;line-height:25px;margin-bottom:10px}
.feature p{font-size:14.5px;line-height:24px;color:#333}
.feature.active{left:362px;top:191px;width:240px;height:329px;background:var(--forest);color:var(--white);padding:22px 15px 0}
.feature.active p{color:var(--white)}
.feature.active .icon{border-color:var(--lime);background:var(--lime)}
.learn-pill{position:absolute;left:62px;bottom:-18px;width:116px;height:38px;border-radius:19px;background:var(--white);color:var(--lime);font-size:14px;display:flex;align-items:center;justify-content:center}
.arrow{position:absolute;top:360px;font-size:22px;color:#222}

/* benefits */
.benefits .section-title{top:2100px;font-size:36px;line-height:44px}
.blob{left:330px;top:2330px;width:620px;height:250px;border-radius:50%;background:radial-gradient(ellipse at center,var(--lime-soft) 0%,rgba(244,247,200,0) 70%)}
.benefit-shot{left:488px;top:2218px;width:226px;height:409px;border-radius:28px;background:linear-gradient(180deg,#f4f4f4 0 20%,#3f8b35 20%,#2c6b28 100%)}
.benefit{position:absolute;width:345px}
.benefit h3{font-size:22px;display:flex;align-items:center;gap:10px;margin-bottom:8px}
.benefit p{font-size:14.5px;line-height:24px;color:#333}
.benefit.left{text-align:right}
.benefit.left h3{justify-content:flex-end}
.tick{width:20px;height:20px;flex:none}

/* testimonial */
.testimonial{left:0;top:2704px;width:1200px;height:431px;background:linear-gradient(90deg,#cfdc2c 0%,#a9c52f 35%,#5f9a36 70%,#3c7c2d 100%)}
.t-heading{position:absolute;left:101px;top:2877px;color:var(--white);font-size:36px;line-height:43px}
.t-title{position:absolute;left:504px;top:2774px;color:var(--white);font-family:"Josefin Sans",sans-serif;font-weight:600;font-size:24px}
.t-text{position:absolute;left:504px;top:2858px;width:560px;color:var(--white);font-size:14.5px;line-height:27px}
.t-name{position:absolute;left:504px;top:3008px;color:var(--white);font-size:19px;font-weight:700}
.dots{position:absolute;left:504px;top:3052px;display:flex;gap:4px}
.dots span{width:11px;height:11px;border-radius:50%;border:1.5px solid var(--white)}
.dots span.on{background:var(--white)}

/* learn more */
.learn-shot{left:65px;top:3209px;width:475px;height:376px;border-radius:30px;background:linear-gradient(180deg,#f6f9d9 0%,#4a8f36 35%,#2c6b28 100%)}
.learn-title{position:absolute;left:630px;top:3196px;font-size:36px;line-height:43px}
.learn-text{position:absolute;left:630px;top:3294px;width:450px;font-size:14.5px;line-height:26.6px;color:#333}
.btn-forest{position:absolute;left:630px;top:3552px;width:136px;height:46px;border-radius:23px;background:var(--forest);color:var(--lime);font-size:15px;font-weight:700;display:flex;align-items:center;justify-content:center}

/* footer */
.footer{position:absolute;left:0;top:3683px;width:1200px;height:533px;background:var(--black);color:var(--white)}
.footer .brand{left:146px;top:98px;font-size:34px}
.footer .brand i{width:22px;height:22px}
.news-title{position:absolute;left:466px;top:66px;font-size:32px}
.news-input{position:absolute;left:471px;top:123px;width:434px;height:54px;border:1px solid var(--white);padding-left:36px;display:flex;align-items:center;font-size:15px}
.news-btn{position:absolute;left:905px;top:123px;width:184px;height:54px;background:var(--forest);display:flex;align-items:center;justify-content:center;font-weight:700;font-size:15px}
.f-col{position:absolute;top:232px}
.f-col h4{font-family:"Lato",sans-serif;font-weight:700;font-size:18px;margin-bottom:18px}
.f-col li{list-style:none;font-size:14.5px;line-height:30px}
.f-col p{font-size:14.5px;line-height:24px;width:260px}
.cards{display:flex;gap:8px;margin-top:16px}
.cards span{width:26px;height:18px;border-radius:3px;background:#ccc}
.socials{display:flex;gap:7px}
.socials span{width:32px;height:32px;border-radius:50%;border:2px solid var(--white);display:flex;align-items:center;justify-content:center}
.socials span i{width:10px;height:10px;border-radius:50%;background:var(--white)}
.copyright{position:absolute;left:0;top:473px;width:1200px;text-align:center;font-size:15px}
</style>
</head>
<body>

<header class="hero">
  <div class="brand"><i></i>Green Vigor</div>
  <nav class="nav"><span>Home</span><span>About Us</span><span>Store</span><span>Blog</span><span>Contact Us</span></nav>
  <div class="account"><span>Login</span><span>|</span><span>Cart</span></div>
  <div class="cart-dot"></div>
  <h1>Green Vigor<br>that is 100% vegan</h1>
  <p>Lorem ipsum dolor sit amet, consectetur adipiscing elit, sed do eiusmod tempor incididunt ut labore et dolore</p>
  <div class="btn-lime">Shop Now</div>
  <div class="hero-circle"></div>
  <div class="placeholder hero-product" role="img" aria-label="Three Green Vigor supplement bottles"></div>
</header>

<section class="product">
  <div class="thumb active" style="top:797px"><i></i></div>
  <div class="thumb" style="top:905px"><i></i></div>
  <div class="thumb" style="top:1015px"><i></i></div>
  <div class="main-shot"><div class="placeholder" role="img" aria-label="Green Vigor supplement bottle, 90 tablets"></div></div>
  <h2 class="product-title">Green Vigor</h2>
  <div class="product-sub">Lorem ipsum dolor sit amet, consectetur</div>
  <div class="stars" style="left:615px;top:882px">
    <svg viewBox="0 0 20 20"><path d="M10 1l2.6 6 6.4.5-4.9 4.2 1.5 6.3L10 14.6 4.4 18l1.5-6.3L1 7.5l6.4-.5z"/></svg>
    <svg viewBox="0 0 20 20"><path d="M10 1l2.6 6 6.4.5-4.9 4.2 1.5 6.3L10 14.6 4.4 18l1.5-6.3L1 7.5l6.4-.5z"/></svg>
    <svg viewBox="0 0 20 20"><path d="M10 1l2.6 6 6.4.5-4.9 4.2 1.5 6.3L10 14.6 4.4 18l1.5-6.3L1 7.5l6.4-.5z"/></svg>
    <svg viewBox="0 0 20 20"><path d="M10 1l2.6 6 6.4.5-4.9 4.2 1.5 6.3L10 14.6 4.4 18l1.5-6.3L1 7.5l6.4-.5z"/></svg>
    <svg viewBox="0 0 20 20"><path d="M10 1l2.6 6 6.4.5-4.9 4.2 1.5 6.3L10 14.6 4.4 18l1.5-6.3L1 7.5l6.4-.5z"/></svg>
  </div>
  <div class="size-label">Size:&nbsp; Packs of 1</div>
  <div class="pack active" style="left:619px;width:105px">Pack of 1</div>
  <div class="pack" style="left:742px;width:103px">Pack of 2</div>
  <div class="pack" style="left:858px;width:103px">Pack of 3</div>
  <div class="qty">Quantity</div>
  <div class="qty-box"><span>-</span><span>01</span><span>+</span></div>
  <div class="btn-lime cart-btn">Add to Cart</div>
  <div class="price">$89.000</div>
  <div class="rule"></div>
  <h3 class="details-title">Product Details</h3>
  <p class="details-text">Lorem ipsum dolor sit amet, consectetur adipiscing elit, sed do eiusmod tempor incididunt ut labore et dolore magna aliqua. Quis ipsum suspendisse</p>
</section>

<section class="features">
  <h2 class="section-title">Green Vigor - A Powerful Supplement<br>for Getting Optimal Health</h2>
  <div class="arrow" style="left:48px">&#8249;</div>
  <div class="arrow" style="left:1138px">&#8250;</div>
  <div class="feature" style="left:114px">
    <div class="icon"><svg width="30" height="30" viewBox="0 0 30 30" fill="none" stroke="#285a25" stroke-width="2"><circle cx="12" cy="17" r="8"/><path d="M18 12l8-8M20 4h6v6"/></svg></div>
    <h3>It May Help Increase Energy (ATP) and Regulate Metabolism</h3>
    <p>Thiamine2, riboflavin3, spirulina algae4, and other B vitamins added in this supplement may help the body convert</p>
  </div>
  <div class="feature active">
    <div class="icon"><svg width="30" height="30" viewBox="0 0 30 30" fill="none" stroke="#fff" stroke-width="2"><circle cx="10" cy="10" r="5"/><circle cx="20" cy="12" r="5"/><circle cx="14" cy="21" r="5"/></svg></div>
    <h3>It May Help the Formation of Red Blood Cells</h3>
    <p>Iron5 (an essential element of red blood cells) and vitamin B123 added in the blend helps your body form red blood cells.</p>
    <div class="learn-pill">Learn More</div>
  </div>
  <div class="feature" style="left:640px">
    <div class="icon"><svg width="30" height="30" viewBox="0 0 30 30" fill="none" stroke="#285a25" stroke-width="2"><path d="M8 26v-6a9 9 0 1 1 14-3l2 3h-3v4h-5v2"/></svg></div>
    <h3>It May Help Improve Mental Health</h3>
    <p>Gotu Kola27 (herb of longevity) added in Green Vigor may help improve the cognitive function and take care</p>
  </div>
  <div class="feature" style="left:889px">
    <div class="icon"><svg width="30" height="30" viewBox="0 0 30 30" fill="none" stroke="#285a25" stroke-width="2"><rect x="7" y="5" width="14" height="20" rx="2"/><path d="M11 11h6M11 16h6M21 14h4"/></svg></div>
    <h3>It May Help Manage Blood Sugar Levels</h3>
    <p>Magnesium35, barley36, raspberries37, broccoli38, safflower39, apples40, etc., present in this supplement contain fiber contents</p>
  </div>
</section>

<section class="benefits">
  <h2 class="section-title">The Benefits Of The<br>Green Vigor</h2>
  <div class="placeholder blob"></div>
  <div class="placeholder benefit-shot" role="img" aria-label="Green Vigor supplement bottle"></div>
  <div class="benefit left" style="left:103px;top:2286px">
    <h3>Safety <svg class="tick" viewBox="0 0 20 20"><circle cx="10" cy="10" r="10" fill="#285a25"/><path d="M5.5 10.5l3 3 6-6.5" stroke="#fff" stroke-width="2.2" fill="none"/></svg></h3>
    <p>Lorem ipsum dolor sit amet, consectetur adipiscing elit, sed do eiusmod tempor incididunt ut labore et dolore magna aliqua.</p>
  </div>
  <div class="benefit left" style="left:103px;top:2458px">
    <h3>Natural energy <svg class="tick" viewBox="0 0 20 20"><circle cx="10" cy="10" r="10" fill="#285a25"/><path d="M5.5 10.5l3 3 6-6.5" stroke="#fff" stroke-width="2.2" fill="none"/></svg></h3>
    <p>Lorem ipsum dolor sit amet, consectetur adipiscing elit, sed do eiusmod tempor incididunt ut labore et dolore magna aliqua.</p>
  </div>
  <div class="benefit" style="left:722px;top:2286px">
    <h3><svg class="tick" viewBox="0 0 20 20"><circle cx="10" cy="10" r="10" fill="#285a25"/><path d="M5.5 10.5l3 3 6-6.5" stroke="#fff" stroke-width="2.2" fill="none"/></svg> Quality</h3>
    <p style="padding-left:33px">Lorem ipsum dolor sit amet, consectetur adipiscing elit, sed do eiusmod tempor incididunt ut labore et dolore magna aliqua.</p>
  </div>
  <div class="benefit" style="left:722px;top:2458px">
    <h3><svg class="tick" viewBox="0 0 20 20"><circle cx="10" cy="10" r="10" fill="#285a25"/><path d="M5.5 10.5l3 3 6-6.5" stroke="#fff" stroke-width="2.2" fill="none"/></svg> Healthy</h3>
    <p style="padding-left:33px">Lorem ipsum dolor sit amet, consectetur adipiscing elit, sed do eiusmod tempor incididunt ut labore et dolore magna aliqua.</p>
  </div>
</section>

<section>
  <div class="placeholder testimonial" role="img" aria-label="Backdrop photo of a person preparing a green smoothie in a blender"></div>
  <h2 class="t-heading">Who Experiences<br>Recommends</h2>
  <div class="t-title">Lorem ipsum dolor sit amet, consectetur</div>
  <div class="stars" style="left:505px;top:2820px">
    <svg viewBox="0 0 20 20"><path d="M10 1l2.6 6 6.4.5-4.9 4.2 1.5 6.3L10 14.6 4.4 18l1.5-6.3L1 7.5l6.4-.5z"/></svg>
    <svg viewBox="0 0 20 20"><path d="M10 1l2.6 6 6.4.5-4.9 4.2 1.5 6.3L10 14.6 4.4 18l1.5-6.3L1 7.5l6.4-.5z"/></svg>
    <svg viewBox="0 0 20 20"><path d="M10 1l2.6 6 6.4.5-4.9 4.2 1.5 6.3L10 14.6 4.4 18l1.5-6.3L1 7.5l6.4-.5z"/></svg>
    <svg viewBox="0 0 20 20"><path d="M10 1l2.6 6 6.4.5-4.9 4.2 1.5 6.3L10 14.6 4.4 18l1.5-6.3L1 7.5l6.4-.5z"/></svg>
    <svg viewBox="0 0 20 20"><path d="M10 1l2.6 6 6.4.5-4.9 4.2 1.5 6.3L10 14.6 4.4 18l1.5-6.3L1 7.5l6.4-.5z"/></svg>
  </div>
  <p class="t-text">Lorem ipsum dolor sit amet, consectetur adipiscing elit, sed do eiusmod tempor incididunt ut labore et dolore magna aliqua. Quis ipsum suspendisse ultrices gravida. Risus commodo viverra maecenas accumsan lacus vel facilisis. Lorem ipsum dolor sit amet, consectetur adipiscing elit, sed do eiusmod tempor incididunt ut labore et dolore magna aliqua.</p>
  <div class="t-name">Marlon Hayes, 57 years old</div>
  <div class="dots"><span></span><span class="on"></span><span></span><span></span><span></span></div>
</section>

<section>
  <div class="placeholder learn-shot" role="img" aria-label="Two Green Vigor bottles over a soft lime brush stroke"></div>
  <h2 class="learn-title">Learn More About The<br>Green Vigor</h2>
  <p class="learn-text">Lorem ipsum dolor sit amet, consectetur adipiscing elit, sed do eiusmod tempor incididunt ut labore et dolore magna aliqua. Quis ipsum suspendisse ultrices gravida. Risus commodo viverra maecenas accumsan lacus vel facilisis. Lorem ipsum dolor sit amet, consectetur adipiscing elit, sed do eiusmod tempor incididunt ut labore et dolore magna aliqua. Quis ipsum suspendisse ultrices gravida. Risus commodo viverra maecenas accumsan lacus vel facilisis. Lorem ipsum dolor sit amet, consectetur adipiscing elit, sed do eiusmod</p>
  <div class="btn-forest">Learn More</div>
</section>

<footer class="footer">
  <div class="brand"><i></i>Green Vigor</div>
  <h2 class="news-title">Sign Up Our Newsletter</h2>
  <div class="news-input">Enter Your Email</div>
  <div class="news-btn">Subscribe</div>
  <div class="f-col" style="left:146px">
    <h4>Accepted Payment Methods</h4>
    <p>Lorem ipsum dolor sit amet, consectetur adipiscing elit, sed do eiusmod tempor incididunt ut labore</p>
    <div class="cards"><span></span><span></span><span></span><span></span><span></span><span></span><span></span></div>
  </div>
  <div class="f-col" style="left:480px">
    <h4>Quick Link</h4>
    <ul><li>Home</li><li>About Us</li><li>Store</li><li>Blog</li><li>Contact Us</li></ul>
  </div>
  <div class="f-col" style="left:679px">
    <h4>Help Link</h4>
    <ul><li>Support / Contact</li><li>Privacy Policies</li><li>Terms of use</li><li>Return Policy</li></ul>
  </div>
  <div class="f-col" style="left:905px">
    <h4>Follow Us</h4>
    <div class="socials"><span><i></i></span><span><i></i></span><span><i></i></span><span><i></i></span></div>
  </div>
  <div class="copyright">© Copyrights 2022 Green Vigor &nbsp;|&nbsp; All Rights Reserved</div>
</footer>

</body>
</html>
```